Business cards for KORU Real Estate Holdings LLC

We need a cool, original business card design for a company based in the Washington DC metropolitan area. We are a new energetic and passionate Real Estate Investing Company that invests in all types of real estate; commercial, residential, industrial etc.

Our company color is Red since it reflects action, energy and speed; it is assertive confident, energizing, exciting, powerful, passionate and determined. So we would like business card communicate those qualities to the audience.

Our audiences are investors that want to invest with us, real estate sellers, buyers, and tenants who lease from us.

Our logo is attached

```html
<!DOCTYPE html>
<html lang="en">
<head>
<meta charset="utf-8">
<title>KORU Real Estate Holdings LLC — Business Cards</title>
<link rel="stylesheet" href="https://fonts.googleapis.com/css2?family=Open+Sans:wght@400;600&display=swap">
<style>
  :root {
    --backdrop: #eeebe5;
    --card: #0b0b0b;
    --ink: #ffffff;
    --ink-soft: #e6e6e6;
    --accent: #c8302b;
    --shadow: rgba(0, 0, 0, 0.35);
  }
  * { box-sizing: border-box; margin: 0; padding: 0; }
  html, body {
    width: 1200px;
    height: 960px;
    overflow: hidden;
    background: var(--backdrop);
    font-family: "Open Sans", Arial, sans-serif;
  }
  .sheet {
    position: relative;
    width: 1200px;
    height: 960px;
  }
  .card {
    position: absolute;
    left: 200px;
    width: 800px;
    height: 440px;
    background: var(--card);
    box-shadow: 0 10px 24px var(--shadow);
    color: var(--ink);
  }
  .card--front { top: 30px; }
  .card--back { top: 490px; }

  .brand {
    position: absolute;
    display: flex;
    align-items: center;
    gap: 22px;
  }
  .brand__mark {
    width: 46px;
    height: 46px;
    background: var(--accent);
    flex: none;
  }
  .brand__name {
    font-weight: 600;
    color: var(--ink);
    line-height: 1.05;
    text-transform: uppercase;
  }
  .brand__name span { display: block; }

  .card--front .brand {
    left: 50%;
    top: 50%;
    transform: translate(-50%, -50%);
  }
  .card--front .brand__name .brand__title { font-size: 96px; letter-spacing: 4px; }
  .card--front .brand__name .brand__sub { font-size: 30px; letter-spacing: 0.5px; }

  .card--back .brand {
    left: 70px;
    top: 50%;
    transform: translateY(-50%);
  }
  .card--back .brand__mark { width: 34px; height: 34px; }
  .card--back .brand__name .brand__title { font-size: 70px; letter-spacing: 3px; }
  .card--back .brand__name .brand__sub { font-size: 22px; letter-spacing: 0.3px; }

  .divider {
    position: absolute;
    left: 455px;
    top: 80px;
    width: 3px;
    height: 270px;
    background: linear-gradient(to bottom, transparent, var(--accent) 35%, var(--accent) 65%, transparent);
  }
  .contacts {
    position: absolute;
    left: 478px;
    top: 140px;
    list-style: none;
  }
  .contacts__item {
    display: flex;
    align-items: center;
    gap: 14px;
    height: 32px;
    font-size: 16px;
    color: var(--ink-soft);
  }
  .contacts__icon {
    width: 16px;
    height: 16px;
    flex: none;
    fill: var(--ink-soft);
  }
</style>
</head>
<body>
<main class="sheet">
  <section class="card card--front" aria-label="Business card front">
    <div class="brand">
      <div class="brand__mark" aria-hidden="true"></div>
      <p class="brand__name"><span class="brand__title">KORU</span><span class="brand__sub">Real Estate Holdings LLC</span></p>
    </div>
  </section>

  <section class="card card--back" aria-label="Business card back">
    <div class="brand">
      <div class="brand__mark" aria-hidden="true"></div>
      <p class="brand__name"><span class="brand__title">KORU</span><span class="brand__sub">Real Estate Holdings LLC</span></p>
    </div>
    <div class="divider" aria-hidden="true"></div>
    <ul class="contacts">
      <li class="contacts__item">
        <svg class="contacts__icon" viewBox="0 0 16 16" aria-hidden="true"><rect x="4" y="0" width="8" height="16" rx="2"/></svg>
        <span>20 2555 0148</span>
      </li>
      <li class="contacts__item">
        <svg class="contacts__icon" viewBox="0 0 16 16" aria-hidden="true"><path d="M1 6c0-2 3-3 7-3s7 1 7 3v1h-4V5.5H5V7H1z"/><rect x="2" y="8" width="12" height="6" rx="1"/></svg>
        <span>20 2555 0193</span>
      </li>
      <li class="contacts__item">
        <svg class="contacts__icon" viewBox="0 0 16 16" aria-hidden="true"><path d="M1 3h14v10H1z M2.5 4.5 8 9l5.5-4.5z" fill-rule="evenodd"/></svg>
        <span>info@korurealestate.com</span>
      </li>
      <li class="contacts__item">
        <svg class="contacts__icon" viewBox="0 0 16 16" aria-hidden="true"><path d="M8 1a7 7 0 1 0 0 14A7 7 0 0 0 8 1zm0 1.5c.9 1 1.5 2.6 1.6 4.5H6.4C6.5 5.1 7.1 3.5 8 2.5zM2.6 7h2.3c.1-1.6.5-3 1.1-4A5.5 5.5 0 0 0 2.6 7zm0 2A5.5 5.5 0 0 0 6 13c-.6-1-1-2.4-1.1-4zm3.8 0h3.2c-.1 1.9-.7 3.5-1.6 4.5-.9-1-1.5-2.6-1.6-4.5zm4.7 0c-.1 1.6-.5 3-1.1 4a5.5 5.5 0 0 0 3.4-4zm2.3-2A5.5 5.5 0 0 0 10 3c.6 1 1 2.4 1.1 4z" fill-rule="evenodd"/></svg>
        <span>www.korurealestate.com</span>
      </li>
      <li class="contacts__item">
        <svg class="contacts__icon" viewBox="0 0 16 16" aria-hidden="true"><path d="M8 0a5.5 5.5 0 0 0-5.5 5.5C2.5 10 8 16 8 16s5.5-6 5.5-10.5A5.5 5.5 0 0 0 8 0zm0 3.5a2 2 0 1 1 0 4 2 2 0 0 1 0-4z" fill-rule="evenodd"/></svg>
        <span>area,state,zipcode,country</span>
      </li>
    </ul>
  </section>
</main>
</body>
</html>
```